Paraffin Wax Packaging Design for Nail and Beauty Industry

We need an attractive design for the packaging of our new product, Paraffin Wax. Our company is a wholesale beauty/nail supply company that has been selling to nail salons in the US market for 10 years. We currently sell this product that we buy from another company. Now we want to launch our own brand of Paraffin Wax.

Target Market(s)

Retail nail salons in the US market.

Industry/Entity Type

Industry

Font styles to use
Sans Serif

Colors

Designer to choose colors to be used in the design.

Requirements
Must have
• Our logo (attached).
• All information on the "Ingredient List" (attached).
• Design for Clear Packaging so product can show through.
• Design for Package Dimensions of 4.25" x 11" (110cm x 280 cm).
Nice to have
• Picture related to women's skin and or beauty.
• Contrast as in the design of product that we currently sell (attached).

```html
<!DOCTYPE html>
<html lang="en">
<head>
<meta charset="utf-8">
<title>Velora Premium Paraffin Wax – Package Front</title>
<link rel="stylesheet" href="https://fonts.googleapis.com/css2?family=Montserrat:wght@800&family=Noto+Serif:wght@400;700&family=Questrial&display=swap">
<style>
  :root {
    --indigo: #433c92;
    --ink: #222222;
    --ring: #2e2e30;
    --paper: #ffffff;
    --wave: #4a6fd8;
    --skin-a: #f1d3bf;
    --skin-b: #e6b89c;
  }
  * { margin: 0; padding: 0; box-sizing: border-box; }
  html, body {
    width: 1120px; height: 1200px; overflow: hidden;
    background: var(--paper);
  }
  .canvas { position: relative; width: 1120px; height: 1200px; }
  .package {
    position: absolute; left: 334px; top: 20px;
    width: 497px; height: 1275px;
    transform: scale(0.91); transform-origin: 0 0;
    background: var(--paper); overflow: hidden;
  }
  .package-art { position: absolute; inset: 0; }
  .brand-name {
    position: absolute; left: 0; top: 72px; width: 497px;
    text-align: center;
    font-family: "Noto Serif", serif; font-weight: 700;
    font-size: 64px; color: var(--ink);
  }
  .product-title {
    position: absolute; left: 0; top: 222px; width: 497px;
    text-align: center; color: var(--paper);
    font-family: "Montserrat", sans-serif; font-weight: 800;
    font-size: 54px; line-height: 58px;
  }
  .claim {
    position: absolute; right: 59px; top: 443px;
    text-align: right; color: var(--ink);
    font-family: "Noto Serif", serif; font-weight: 700;
    font-size: 29px; line-height: 41px;
  }
  .benefit {
    position: absolute; right: 59px; top: 618px;
    text-align: right; color: var(--ink);
    font-family: "Noto Serif", serif; font-weight: 400;
    font-size: 21px; line-height: 30px;
  }
  .label-info {
    position: absolute; left: 0; top: 1103px; width: 497px;
    text-align: center; color: var(--ink);
  }
  .ingredients-title { font-family: "Noto Serif", serif; font-weight: 700; font-size: 17px; line-height: 22px; }
  .ingredients-list { font-family: "Noto Serif", serif; font-size: 15px; line-height: 21px; }
  .caution { font-family: "Questrial", sans-serif; font-size: 13.5px; line-height: 18px; margin-top: 5px; }
  .net-weight { font-family: "Questrial", sans-serif; font-size: 18px; margin-top: 14px; }
</style>
</head>
<body>
<div class="canvas">
  <section class="package">
    <svg class="package-art" width="497" height="1275" viewBox="0 0 497 1275">
      <defs>
        <linearGradient id="skinTone" x1="0" y1="0" x2="1" y2="1">
          <stop offset="0" stop-color="var(--skin-a)"/>
          <stop offset="1" stop-color="var(--skin-b)"/>
        </linearGradient>
      </defs>
      <rect class="header-band" x="0" y="0" width="497" height="437" fill="var(--indigo)"/>
      <circle class="ring-outer" cx="300" cy="582" r="227" fill="var(--ring)"/>
      <circle class="ring-inner" cx="314" cy="590" r="214" fill="var(--paper)"/>
      <ellipse class="brand-oval" cx="248" cy="117" rx="235" ry="88" fill="var(--paper)"/>
      <rect class="hero-photo" role="img" aria-label="Photo of a woman in a white top seated with smooth bare legs"
            x="12" y="745" width="483" height="278" rx="14" fill="url(#skinTone)"/>
      <rect class="divider" x="40" y="1058" width="417" height="4" rx="2" fill="var(--wave)"/>
    </svg>
    <div class="brand-name">Velora</div>
    <h1 class="product-title">PREMIUM<br>PARAFFIN WAX</h1>
    <p class="claim">Compatible for<br>use with most<br>wax paraffin heat<br>therapy units.</p>
    <p class="benefit">Deeply Moisturizes<br>the Skin Restoring<br>a Healthier Look<br>and Feel to Skin.</p>
    <div class="label-info">
      <p class="ingredients-title">Ingredients:</p>
      <p class="ingredients-list">Paraffin waxes and Hydrocarbon waxes, Petrolatum,<br>Paraffin oils, Apricot kernel oil, Fragrance D &amp; C dyes.</p>
      <p class="caution">Caution:<br>Paraffin is flammable. Do not use<br>near open flame or an unprotected resistance heater.</p>
      <p class="net-weight">Net Wt. 1 lb. (450 g.)</p>
    </div>
  </section>
</div>
</body>
</html>
```